Need a new updated business logo and business cards and possible car signs. Logo should be modern with bold elements. Possible use in some way of former logo may be considered. Looking for use of bold colors to grab attention with car signage/wrap in mind. Phone number should be easy to read- customers should understand what business is about- home painting, repair, renovation, 're-imagine your space' etc.

Target Market(s)

Homeowners, construction, businesses

Industry/Entity Type

Contractor

Contact Information for Business Card

Brennick Painting & Renovation, Inc.
Owner : Marcus D. Brennick
555-014-7382
marcusdbrennickmb@quillpost.net
All work is guaranteed and insured! More than 30 years of experience:
residential & commercial, Interior & Exterior, Renovation/Restoration

Logo Text

Brennick Painting & Renovation, Inc. 'Hard Working & Trustworthy'

Font styles to use
Other font styles liked:
• Designer suggestions for industry

Colors

Designer to choose colors to be used in the design.

Requirements
Must have
• New design logo-possibly incorporating old elements- new logo ok without old though as well. Cell Phone number has to be on there- Color preferable
Nice to have
• Nice to have a logo that pops and that may be used in conjunction with his parent company Brennick REAL Property, LLC.
• Business card layout of information that is clear & easy to read
Should not have
• Bulky old fonts

```html
<!DOCTYPE html>
<html lang="en">
<head>
<meta charset="utf-8">
<title>Brennick Painting &amp; Renovation – Business Cards</title>
<link rel="stylesheet" href="https://fonts.googleapis.com/css2?family=Cinzel:wght@500&family=Lato:wght@400;700&display=swap">
<style>
  :root {
    --navy: #123a66;
    --navy-dark: #0f3562;
    --ink: #1d1d1d;
    --white: #ffffff;
    --backdrop: #5b5b5b;
    --rule: #c9c9c9;
  }
  * { margin: 0; padding: 0; box-sizing: border-box; }
  html, body { width: 1200px; height: 802px; overflow: hidden; }
  body { background: var(--backdrop); font-family: "Lato", sans-serif; position: relative; }

  .card {
    position: absolute;
    top: 274px;
    width: 443px;
    height: 265px;
    box-shadow: 2px 3px 6px rgba(0,0,0,0.45);
  }
  .card--front { left: 136px; background: var(--white); }
  .card--back { left: 624px; background: var(--navy-dark); color: var(--white); text-align: center; }

  .brand-mark {
    position: absolute;
    left: 28px;
    top: 92px;
    width: 170px;
    text-align: center;
    color: var(--navy);
    font-weight: 700;
    font-size: 17px;
    line-height: 1.2;
  }
  .brand-mark__square {
    display: block;
    width: 26px;
    height: 26px;
    margin: 0 auto 10px;
    background: var(--navy);
  }

  .divider {
    position: absolute;
    left: 218px;
    top: 72px;
    width: 1px;
    height: 118px;
    background: var(--rule);
  }

  .contact {
    position: absolute;
    left: 236px;
    top: 80px;
    color: var(--ink);
    font-size: 12.5px;
    line-height: 1.3;
  }
  .contact__name {
    font-family: "Cinzel", serif;
    font-weight: 500;
    color: var(--navy);
    font-size: 15.5px;
    letter-spacing: 0.4px;
    line-height: 1.05;
  }
  .contact__role { margin-left: 2px; margin-bottom: 9px; }
  .contact__address { margin-bottom: 6px; }
  .contact__line { display: flex; align-items: center; gap: 3px; }
  .contact__line svg { width: 11px; height: 11px; fill: var(--ink); flex: none; }
  .contact__email { font-size: 11.6px; }

  .guarantee {
    position: absolute;
    left: 0;
    right: 0;
    top: 222px;
    text-align: center;
    color: var(--navy);
    font-weight: 700;
    font-size: 12.5px;
  }

  .back__name {
    margin-top: 72px;
    font-size: 23px;
    font-weight: 700;
    line-height: 1.15;
    letter-spacing: 0.3px;
    padding: 0 30px;
  }
  .back__experience { margin-top: 24px; font-size: 13px; }
  .back__services { margin-top: 14px; font-size: 13px; line-height: 1.4; }
</style>
</head>
<body>
  <section class="card card--front" aria-label="Business card front">
    <div class="brand-mark">
      <span class="brand-mark__square"></span>
      Brennick Painting &amp; Renovation, Inc.
    </div>
    <div class="divider"></div>
    <div class="contact">
      <p class="contact__name">MARCUS D. BRENNICK</p>
      <p class="contact__role">Owner</p>
      <p class="contact__address">48 Harlow Lane<br>Milbrook, NC 27999</p>
      <p class="contact__line">
        <svg viewBox="0 0 24 24" aria-hidden="true"><path d="M6.6 10.8a15.1 15.1 0 0 0 6.6 6.6l2.2-2.2c.3-.3.7-.4 1-.2 1.1.4 2.3.6 3.6.6.6 0 1 .4 1 1V20c0 .6-.4 1-1 1A17 17 0 0 1 3 4c0-.6.4-1 1-1h3.5c.6 0 1 .4 1 1 0 1.3.2 2.5.6 3.6.1.3 0 .7-.2 1z"/></svg>
        555-014-7382
      </p>
      <p class="contact__line contact__email">
        <svg viewBox="0 0 24 24" aria-hidden="true"><path d="M2 5h20v14H2z M3.5 6.5 12 13l8.5-6.5" fill-rule="evenodd"/><path d="M2 5l10 8 10-8v14H2z"/></svg>
        marcusdbrennickmb@quillpost.net
      </p>
    </div>
    <p class="guarantee">ALL WORK IS GUARANTEED AND INSURED!</p>
  </section>

  <section class="card card--back" aria-label="Business card back">
    <p class="back__name">BRENNICK PAINTING &amp; RENOVATION, INC.</p>
    <p class="back__experience">MORE THAN 30 YEARS OF EXPERIENCE.</p>
    <p class="back__services">RESIDENTIAL &amp; COMMERCIAL<br>INTERIOR &amp; EXTERIOR<br>RENOVATION/RESTORATION</p>
  </section>
</body>
</html>
```